Corporate Travel Technology Company needs new Business Card design

We need a new business card design to reflect our re-branded company. Our company is called tolvEn (pronounced tolvenn) and we provide Business Intelligence and Smart Corporate Journeys solutions for the corporate travel industry. Our multinational customers use our solutions to manage large travel budgets and frequent travellers, as well as to save money and reduce risk. We'd like to see designs that use the blue and green palette as well as our corporate logo (attached below). The design should communicate innovation, insight, forward thinking, contemporary, trusted.

Target Market(s)

Large multinational corporates and Travel Agencies.

Industry/Entity Type

Business

Contact Information for Business Card

Rosalind Mercer
Chief Executive
tolvEn
Phone number - +61 (0)2 8134 2907
Email address - rosalind.mercer@tolven-example.com
Mobile number - +61 (0)438 516 702
www.tolven-example.com

Font styles to use
Other font styles liked:
• Please use font as close to corporate logo as possible

Colors
0255a3
0393ce
00a990
33b8a4
33a6d7
3176b5

Requirements
Must have
• Please include the words;
• Smart Corporate Journeys
• Clearer Insight for Every Trip Taken
• Use corporate logo - although icon can be stylised if needed

```html
<!DOCTYPE html>
<html lang="en">
<head>
<meta charset="utf-8">
<title>tolvEn Business Card</title>
<link rel="stylesheet" href="https://fonts.googleapis.com/css2?family=Source+Sans+3:wght@400;600&family=PT+Serif:wght@700&display=swap">
<style>
  :root {
    --page: #ecebe8;
    --card-dark: #2e3a3b;
    --card-light: #fbfbfa;
    --brand-blue: #1ea6e0;
    --ink-light: #f2f4f4;
    --ink-slate: #3b4748;
    --card-shadow: 0 14px 30px rgba(0, 0, 0, 0.22);
  }
  * { margin: 0; padding: 0; box-sizing: border-box; }
  html, body {
    width: 1200px;
    height: 950px;
    overflow: hidden;
    background: var(--page);
  }
  .canvas {
    position: relative;
    width: 1200px;
    height: 950px;
  }
  .card {
    position: absolute;
    width: 620px;
    height: 360px;
    border-radius: 26px;
    box-shadow: var(--card-shadow);
    overflow: hidden;
  }
  .card-front {
    left: 110px;
    top: 90px;
    background: var(--card-dark);
  }
  .card-back {
    left: 470px;
    top: 500px;
    background: var(--card-light);
  }
  .front-brand {
    position: absolute;
    top: 38px;
    right: 42px;
    display: flex;
    align-items: center;
    gap: 12px;
    font-family: "Source Sans 3", sans-serif;
    font-weight: 600;
    font-size: 34px;
    color: var(--brand-blue);
  }
  .brand-dot {
    width: 22px;
    height: 22px;
    border-radius: 50%;
    background: var(--brand-blue);
  }
  .contact {
    position: absolute;
    left: 44px;
    bottom: 36px;
    font-family: "Source Sans 3", sans-serif;
    color: var(--ink-light);
  }
  .contact-name {
    font-weight: 600;
    font-size: 26px;
    color: var(--brand-blue);
    line-height: 1.1;
  }
  .contact-title {
    font-family: "PT Serif", serif;
    font-weight: 700;
    font-size: 19px;
    margin: 4px 0 10px;
  }
  .contact-line {
    font-size: 15.5px;
    line-height: 1.45;
  }
  .sep { color: var(--brand-blue); padding: 0 5px; }
  .tag-bullet { color: var(--brand-blue); padding: 0 6px; }
  .back-brand {
    position: absolute;
    inset: 0;
    display: flex;
    align-items: center;
    justify-content: center;
    gap: 16px;
    font-family: "Source Sans 3", sans-serif;
    font-weight: 400;
    font-size: 84px;
    letter-spacing: 1px;
    color: var(--ink-slate);
  }
  .back-dot {
    width: 34px;
    height: 34px;
    border-radius: 50%;
    background: var(--brand-blue);
  }
</style>
</head>
<body>
<main class="canvas">
  <section class="card card-front">
    <div class="front-brand"><span class="brand-dot"></span><span>tolvEn</span></div>
    <div class="contact">
      <p class="contact-name">Rosalind Mercer</p>
      <p class="contact-title">Chief Executive</p>
      <p class="contact-line">+61 (0)2 8134 2907<span class="sep">|</span>+61 (0)438 516 702</p>
      <p class="contact-line">rosalind.mercer@tolven-example.com<span class="sep">|</span>www.tolven-example.com</p>
      <p class="contact-line tagline">Smart Corporate Journeys<span class="tag-bullet">&#8226;</span>Clearer Insight for Every Trip Taken</p>
    </div>
  </section>
  <section class="card card-back">
    <div class="back-brand"><span>tolvEn</span><span class="back-dot"></span></div>
  </section>
</main>
</body>
</html>
```